Healthcare and Professional IT Services Company need a redesigned business card

We are a IT Services company that targets small medical practices and professional business such as Attorneys, Accounts, Architects etc. We want to communicate a professional yet friendly image using recent logo redesign here on ArtHarbor. Like to see the colors blue and orange in the design. Must use the Tall Pine Computing as displayed in the new logo - then also want to incorporate the fish logo as well.

Target Market(s)

Small medical and professional services

Industry/Entity Type

It Company

Contact Information for Business Card

The usual stuff, place for name address phone website. Also maybe our tagline which is "Grounded in good support"

Requirements
Must have
• My new logo and the fish somewhere on the card

```html
<!DOCTYPE html>
<html lang="en">
<head>
<meta charset="utf-8">
<title>Tall Pine Computing – Business Card</title>
<link rel="stylesheet" href="https://fonts.googleapis.com/css2?family=Didact+Gothic&family=Open+Sans:wght@400&display=swap">
<style>
  :root {
    --brand-blue: #0099dd;
    --deep-blue: #0b6fb8;
    --accent-orange: #f39a2e;
    --paper: #ffffff;
    --ink-grey: #6b6b6b;
    --backdrop: #d9d9d9;
  }
  * { box-sizing: border-box; margin: 0; padding: 0; }
  html, body { width: 1200px; height: 900px; overflow: hidden; }
  body {
    background: var(--backdrop);
    font-family: "Didact Gothic", sans-serif;
    display: flex;
    flex-direction: column;
    align-items: center;
    justify-content: center;
    gap: 44px;
  }
  .card {
    width: 640px;
    height: 366px;
    position: relative;
    overflow: hidden;
    box-shadow: 0 6px 18px rgba(0,0,0,0.25);
  }

  /* Front */
  .card-front { background: var(--brand-blue); color: var(--paper); }
  .front-brand {
    position: absolute;
    left: 0; right: 0; top: 130px;
    text-align: center;
    font-size: 40px;
    letter-spacing: 1px;
    color: var(--paper);
  }
  .tagline {
    position: absolute;
    left: 150px; top: 262px;
    font-family: "Open Sans", sans-serif;
    font-size: 13px;
  }

  /* Back */
  .card-back { background: var(--paper); }
  .name-band {
    position: absolute;
    left: 0; top: 0; right: 0;
    height: 96px;
    background: var(--brand-blue);
    color: var(--paper);
    padding: 24px 0 0 56px;
  }
  .person-name { font-size: 28px; letter-spacing: 2px; line-height: 1.1; }
  .person-title { font-size: 16px; letter-spacing: 0.5px; }
  .contact {
    position: absolute;
    left: 44px; top: 128px;
    color: var(--ink-grey);
    font-size: 15px;
    letter-spacing: 1px;
    line-height: 1.45;
    list-style: none;
  }
  .contact li { display: flex; align-items: center; gap: 8px; }
  .contact .address { padding-left: 22px; }
  .contact svg { width: 14px; height: 14px; flex: none; fill: var(--brand-blue); }
  .back-brand {
    position: absolute;
    right: 40px; bottom: 44px;
    display: flex;
    align-items: center;
    gap: 12px;
    font-size: 30px;
    color: var(--deep-blue);
  }
  .brand-dot {
    width: 22px; height: 22px;
    border-radius: 50%;
    background: var(--accent-orange);
  }
</style>
</head>
<body>
  <section class="card card-front" aria-label="Business card front">
    <p class="front-brand">Tall Pine Computing</p>
    <p class="tagline">Grounded in good support</p>
  </section>

  <section class="card card-back" aria-label="Business card back">
    <header class="name-band">
      <p class="person-name">Owen Carter</p>
      <p class="person-title">CEO/Founder</p>
    </header>
    <ul class="contact">
      <li class="address">4120 Larkspur Road</li>
      <li class="address">Fairbanks, Alaska 99712</li>
      <li>
        <svg viewBox="0 0 24 24" aria-hidden="true"><path d="M6.6 10.8a15.1 15.1 0 0 0 6.6 6.6l2.2-2.2a1 1 0 0 1 1-.25 11.4 11.4 0 0 0 3.6.6 1 1 0 0 1 1 1V20a1 1 0 0 1-1 1A17 17 0 0 1 3 4a1 1 0 0 1 1-1h3.5a1 1 0 0 1 1 1c0 1.25.2 2.45.6 3.6a1 1 0 0 1-.25 1z"/></svg>
        555 218 4760
      </li>
      <li>
        <svg viewBox="0 0 24 24" aria-hidden="true"><path d="M2 5h20v14H2z M2 5l10 8 10-8" stroke="#fff" stroke-width="1.5"/></svg>
        owen@tallpinecomputing.com
      </li>
      <li>
        <svg viewBox="0 0 24 24" aria-hidden="true"><circle cx="12" cy="12" r="10"/></svg>
        www.tallpinecomputing.com
      </li>
    </ul>
    <div class="back-brand">
      <span class="brand-dot" aria-hidden="true"></span>
      <span class="brand-name">Tall Pine Computing</span>
    </div>
  </section>
</body>
</html>
```